Business Card for a Jewellery Brand

Business card for an upscale jewellery brand. Attached is the brand logo and icon and color board. I am looking for two card versions: one for the founder and one is generic. The card should be elegant and convey upscale and premium feel. I am open to both square and rectangle card shapes.

Industry/Entity Type

Jewelry

Contact Information for Business Card

Two cards: (1) Sunela Parvaniya (Founder) (2) General
(1) Sunela Parvaniya card should have Name: Sunela Parvaniya, Title: Founder Email id: sunela@quiremo.com.au. Phone no: +61452913307
(2) Generic card should have Email id: info@quiremo.com.au. Phone no: +61436207518

Requirements
Must have
• Workmark
• ICON
• Phone no
• Email ID
• ABN: 58219740312 (Note: ABN is Business number in Australia)
• Website: www.quiremo.com.au
• Instagram: quiremo_jewellery
• Facebook: @quiremojewellery
Nice to have
• Tagline

```html
<!DOCTYPE html>
<html lang="en">
<head>
<meta charset="utf-8">
<title>Quiremo Business Cards</title>
<link href="https://fonts.googleapis.com/css2?family=Jost:wght@400;500&display=swap" rel="stylesheet">
<style>
  :root {
    --backdrop: #1c1c1e;
    --blush: #e49a96;
    --blush-deep: #e0857f;
    --paper: #ffffff;
    --ink: #3a3a3a;
    --social: #8a8fb0;
  }
  * { box-sizing: border-box; margin: 0; padding: 0; }
  html, body {
    width: 1200px; height: 929px; overflow: hidden;
    background: var(--backdrop);
    font-family: "Jost", "Futura", sans-serif;
  }
  .card {
    position: absolute;
    width: 560px; height: 320px;
    box-shadow: 0 10px 28px rgba(0,0,0,0.5);
  }
  .card-front { left: 100px; top: 110px; background: var(--blush); }
  .card-back { left: 540px; top: 490px; background: var(--paper); }
  .card-frame {
    position: absolute; inset: 16px;
    border: 1px solid var(--paper);
  }
  .card-back .card-frame { border-color: var(--blush); }

  .front-brand {
    position: absolute; inset: 0;
    display: flex; flex-direction: column; align-items: center; justify-content: center;
    gap: 14px;
    color: var(--paper);
  }
  .front-mark {
    width: 64px; height: 64px; border-radius: 50%;
    border: 2px solid var(--paper);
  }
  .front-wordmark {
    font-size: 46px; font-weight: 400; letter-spacing: 14px;
    padding-left: 14px; line-height: 1;
  }

  .back-brand {
    position: absolute; left: 30px; top: 0; width: 230px; height: 100%;
    display: flex; flex-direction: column; align-items: center; justify-content: center;
    gap: 14px;
    color: var(--blush);
  }
  .back-mark {
    width: 110px; height: 110px; border-radius: 50%;
    border: 5px solid var(--blush);
  }
  .back-wordmark {
    font-size: 22px; font-weight: 500; letter-spacing: 6px;
    padding-left: 6px; line-height: 1;
  }
  .divider {
    position: absolute; left: 272px; top: 86px;
    width: 1px; height: 162px; background: var(--blush);
  }
  .abn {
    position: absolute; right: 40px; top: 36px;
    font-size: 15px; color: var(--ink); letter-spacing: 0.5px;
  }
  .abn-label { color: var(--blush); margin-right: 4px; font-size: 13px; }
  .contact {
    position: absolute; left: 292px; top: 80px;
  }
  .person-name {
    color: var(--blush); font-size: 19px; font-weight: 500;
    letter-spacing: 1px; text-transform: uppercase; line-height: 1.2;
  }
  .person-title {
    color: var(--ink); font-size: 14px; font-weight: 500;
    letter-spacing: 1px; margin-bottom: 10px;
  }
  .contact-list { list-style: none; }
  .contact-list li {
    display: flex; align-items: center; gap: 9px;
    font-size: 14.5px; color: var(--ink); letter-spacing: 0.5px;
    height: 21px; white-space: nowrap;
  }
  .contact-icon { width: 12px; height: 12px; flex: none; }
  .social-square { width: 11px; height: 11px; background: var(--social); flex: none; margin-right: 1px; }
</style>
</head>
<body>
  <section class="card card-front">
    <div class="card-frame"></div>
    <div class="front-brand">
      <span class="front-mark" role="img" aria-label="Brand icon"></span>
      <div class="front-wordmark">QUIREMO</div>
    </div>
  </section>

  <section class="card card-back">
    <div class="card-frame"></div>
    <div class="back-brand">
      <span class="back-mark" role="img" aria-label="Brand icon"></span>
      <div class="back-wordmark">QUIREMO</div>
    </div>
    <div class="divider"></div>
    <p class="abn"><span class="abn-label">ABN:</span>58219740312</p>
    <div class="contact">
      <p class="person-name">Sunela Parvaniya</p>
      <p class="person-title">FOUNDER</p>
      <ul class="contact-list">
        <li>
          <svg class="contact-icon" viewBox="0 0 12 12"><rect x="3" y="0.5" width="6" height="11" rx="1" fill="none" stroke="#3a3a3a" stroke-width="1"/></svg>
          +61452913307
        </li>
        <li>
          <svg class="contact-icon" viewBox="0 0 12 12"><circle cx="6" cy="6" r="5" fill="none" stroke="#e49a96" stroke-width="1.2"/><path d="M1 6h10M6 1c2 2 2 8 0 10M6 1c-2 2-2 8 0 10" fill="none" stroke="#e49a96" stroke-width="1"/></svg>
          www.quiremo.com.au
        </li>
        <li>
          <svg class="contact-icon" viewBox="0 0 12 12"><rect x="0.5" y="2" width="11" height="8" fill="#e49a96"/><path d="M0.5 2l5.5 4.5L11.5 2" fill="none" stroke="#fff" stroke-width="1"/></svg>
          sunela@quiremo.com.au
        </li>
        <li>
          <svg class="contact-icon" viewBox="0 0 12 12"><circle cx="5" cy="5" r="3.5" fill="none" stroke="#e49a96" stroke-width="1.6"/><path d="M7.5 7.5L11 11" stroke="#e49a96" stroke-width="1.8"/></svg>
          quiremo_jewellery
        </li>
        <li><span class="social-square"></span>@quiremojewellery</li>
      </ul>
    </div>
  </section>
</body>
</html>
```